8x8 Social Media Ad - Brant Summit Expo

Attention Real Estate Agents
Please join us for our
Quarterly Real Estate Training Expo
The 2nd Saturday of February, May, August and November
Our Next Training Expo is _________________________________
From 9 am to 1 pm
at
Halvorne Suites Millbrook Court
4817 Copper Willow Lane, Dunmere, MD 20588
Scheduled Speakers
9:00 am - Marcus Pellington - Orientation
9:30 am - Derrin Oakfield - Multiple Income Streams / Crest Program
10:00 am - Talia Brennick - Marketing though Social Media
10:45 am - Rex Dunmore - Generating Business through Ru-Plaza
11:30 am - Kemi Adeyoro - Real Estate Investing
12:15 pm - Gregor Tamsey - (Main Speaker) Training Topic TBA
For more information call Marcus Pellington at (240) 555-0183 or email mpellington@brantsummithomes.example

```html
<!DOCTYPE html>
<html lang="en">
<head>
<meta charset="utf-8">
<title>Brant Summit Expo – Quarterly Training Expo Ad</title>
<link rel="stylesheet" href="https://fonts.googleapis.com/css2?family=Poppins:wght@400;500;600;700;800;900&display=swap">
<style>
  :root {
    --teal: #14939f;
    --teal-dark: #0e7d88;
    --ink: #1d1d1f;
    --panel: #232325;
    --paper: #e9eaeb;
    --haze: #c3c7ca;
    --white: #ffffff;
    --text-dark: #2a2a2c;
    --stage: #dfe2e4;
  }
  * { margin: 0; padding: 0; box-sizing: border-box; }
  html, body { width: 1200px; height: 800px; overflow: hidden; }
  body { background: var(--stage); font-family: "Poppins", sans-serif; position: relative; }

  .flyer {
    position: absolute; left: 220px; top: 20px;
    width: 760px; height: 760px; overflow: hidden;
    background: linear-gradient(180deg, var(--paper) 0%, var(--haze) 100%);
    box-shadow: 0 10px 30px rgba(0,0,0,.18);
  }
  .skyline {
    position: absolute; left: 300px; top: 0; width: 460px; height: 345px;
    background: linear-gradient(180deg, #e4e6e7 0%, #b9b4ab 55%, #9a958d 100%);
    opacity: .55;
  }
  .shapes { position: absolute; inset: 0; }

  .brand {
    position: absolute; left: 40px; top: 34px;
    display: flex; align-items: center; gap: 8px;
    color: var(--teal); font-weight: 800; font-size: 17px; letter-spacing: .2px;
  }
  .brand-mark { width: 16px; height: 16px; background: var(--teal); }

  .host-photo {
    position: absolute; left: 80px; top: 72px; width: 240px; height: 228px;
    background: linear-gradient(180deg, #8a7f73 0%, #2c3f72 60%, #223260 100%);
  }

  .headline {
    position: absolute; right: 40px; top: 40px; text-align: right;
    color: var(--teal); font-weight: 900; font-size: 56px; line-height: .93;
    text-transform: uppercase; letter-spacing: 1px;
  }
  .schedule-line {
    position: absolute; right: 40px; top: 254px; text-align: right;
    color: var(--text-dark); font-weight: 500; font-size: 17px; line-height: 1.25;
    text-transform: uppercase;
  }
  .headline-phone {
    position: absolute; right: 40px; top: 302px;
    display: flex; align-items: center; gap: 8px;
    color: var(--ink); font-weight: 700; font-size: 22px; line-height: 1.3;
  }
  .headline-phone svg { width: 18px; height: 18px; }

  .band-speaker {
    position: absolute; left: 70px; top: 318px; width: 300px;
    color: var(--white); font-weight: 600; font-size: 12px; line-height: 1.3; text-align: center;
  }

  .invite {
    position: absolute; left: 0; right: 0; top: 388px; text-align: center;
    color: var(--white); font-weight: 800; font-size: 20px; line-height: 1.25; text-transform: uppercase;
  }

  .speakers {
    position: absolute; left: 65px; top: 462px; display: flex; gap: 10px;
  }
  .speaker { width: 118px; }
  .speaker-photo { width: 118px; height: 96px; }
  .speaker-photo.p1 { background: linear-gradient(180deg, #bfc1c3, #3a3a3c); }
  .speaker-photo.p2 { background: linear-gradient(180deg, #7d8693, #e9eaed); }
  .speaker-photo.p3 { background: linear-gradient(180deg, #d8dadd, #2d4a86); }
  .speaker-photo.p4 { background: linear-gradient(180deg, #5e8a45, #3d6491); }
  .speaker-photo.p5 { background: linear-gradient(180deg, #e1ddd6, #2a2a2e); }
  .speaker-time { margin-top: 6px; color: var(--teal); font-weight: 700; font-size: 11.5px; line-height: 1.3; }
  .speaker-info { color: var(--white); font-size: 9.5px; line-height: 1.3; }

  .address {
    position: absolute; left: 40px; top: 684px; width: 370px;
    color: var(--white); font-weight: 500; font-size: 12px; line-height: 1.35; text-transform: uppercase;
  }
  .contact {
    position: absolute; left: 476px; top: 646px;
    color: var(--white); font-weight: 500; font-size: 11.5px; line-height: 1.9; white-space: nowrap;
  }
  .contact-row { display: flex; align-items: center; gap: 8px; }
  .contact-row svg { width: 12px; height: 12px; flex: none; }
</style>
</head>
<body>
<main class="flyer">
  <div class="skyline" role="img" aria-label="Soft city skyline photograph behind the headline"></div>

  <svg class="shapes" viewBox="0 0 760 760" aria-hidden="true">
    <polygon points="0,300 360,300 405,345 760,345 760,760 0,760" fill="var(--panel)"/>
    <polygon points="0,310 352,310 392,352 0,352" fill="var(--teal)"/>
    <polyline points="0,364 415,364 432,355 760,355" fill="none" stroke="var(--teal)" stroke-width="3"/>
    <rect x="0" y="666" width="760" height="94" fill="var(--teal)"/>
    <polygon points="400,620 760,620 760,732 460,732" fill="var(--ink)"/>
    <polygon points="416,630 760,630 760,722 470,722" fill="var(--teal)"/>
  </svg>

  <div class="brand"><span class="brand-mark"></span>Brant Summit Realty</div>

  <div class="host-photo" role="img" aria-label="Portrait photo of host speaker Derrin Oakfield in a blue suit"></div>

  <h1 class="headline">Attention<br>Real<br>Estate<br>Agents</h1>
  <p class="schedule-line">The 2nd Saturday of February<br>May, August and November</p>
  <p class="headline-phone">
    <svg viewBox="0 0 24 24"><path fill="var(--teal)" d="M6.6 10.8a15.1 15.1 0 0 0 6.6 6.6l2.2-2.2c.3-.3.7-.4 1-.2 1.1.4 2.3.6 3.6.6.6 0 1 .4 1 1V20c0 .6-.4 1-1 1A17 17 0 0 1 3 4c0-.6.4-1 1-1h3.5c.6 0 1 .4 1 1 0 1.2.2 2.4.6 3.6.1.3 0 .7-.2 1z"/></svg>
    240-555-0183
  </p>

  <p class="band-speaker">9:30 am - Derrin Oakfield - Multiple<br>Income Streams / Crest Program</p>

  <h2 class="invite">Please join us for our quarterly<br>real estate training expo</h2>

  <section class="speakers">
    <div class="speaker">
      <div class="speaker-photo p1" role="img" aria-label="Photo of Marcus Pellington"></div>
      <p class="speaker-time">9:00 AM</p>
      <p class="speaker-info">Marcus Pellington<br>orientation</p>
    </div>
    <div class="speaker">
      <div class="speaker-photo p2" role="img" aria-label="Photo of Talia Brennick"></div>
      <p class="speaker-time">10:00 AM</p>
      <p class="speaker-info">Talia Brennick<br>marketing though<br>social media</p>
    </div>
    <div class="speaker">
      <div class="speaker-photo p3" role="img" aria-label="Photo of Rex Dunmore"></div>
      <p class="speaker-time">10:45 AM</p>
      <p class="speaker-info">Rex Dunmore -<br>Generating Business<br>through Ru-Plaza</p>
    </div>
    <div class="speaker">
      <div class="speaker-photo p4" role="img" aria-label="Photo of Kemi Adeyoro"></div>
      <p class="speaker-time">11:30 AM</p>
      <p class="speaker-info">Kemi Adeyoro -<br>Real Estate Investing</p>
    </div>
    <div class="speaker">
      <div class="speaker-photo p5" role="img" aria-label="Photo of main speaker Gregor Tamsey"></div>
      <p class="speaker-time">12:15 PM</p>
      <p class="speaker-info">Gregor Tamsey -<br>(Main Speaker) Training<br>Topic TBA</p>
    </div>
  </section>

  <p class="address">Our next training expo is from 9 am to 1 pm at Halvorne Suites Millbrook Court 4817 Copper Willow Lane, Dunmere, MD 20588</p>

  <div class="contact">
    <p class="contact-row">
      <svg viewBox="0 0 24 24"><path fill="var(--white)" d="M6.6 10.8a15.1 15.1 0 0 0 6.6 6.6l2.2-2.2c.3-.3.7-.4 1-.2 1.1.4 2.3.6 3.6.6.6 0 1 .4 1 1V20c0 .6-.4 1-1 1A17 17 0 0 1 3 4c0-.6.4-1 1-1h3.5c.6 0 1 .4 1 1 0 1.2.2 2.4.6 3.6.1.3 0 .7-.2 1z"/></svg>
      240-555-0183
    </p>
    <p class="contact-row">
      <svg viewBox="0 0 24 24"><path fill="var(--white)" d="M2 5h20v14H2zm2 2v.5l8 5 8-5V7l-8 5z"/></svg>
      mpellington@brantsummithomes.example
    </p>
  </div>
</main>
</body>
</html>
```